Etikett für einen Rosé Wein
Zielgruppe
Wir sind ein Weingut und benötigen ein neues Etikett für unseren Muskattrollinger Rosé. Unsere Kunden sind eher traditionelle Weinkäufer.
Aufgabenstellung
Format:
Höhe: 9 cm
Breite: 11 cm
Da es nur ein Vorderetikett gibt, müssen alle relevanten Angaben (Hersteller, Alkohol, Inhalt in L, Rebsorte, etc.) enthalten sein. (siehe Flaschenabbildung anbei)
WÜRTTEMBERG
2019er
Muskattrollinger Rosé
DEUTSCHER QUALITÄTSWEIN
11,0 % Vol.
0,75 l
Enthält Sulfite
A.P.Nr. 58127364
Abfüller
Straße / PLZ / Ort / Tel.
Der Flaschenverschluss ist schwarz d.h. das neue Etikettendesign sollte dazu passen.
Bisher ist der Hintergrund des Weinetiketts schwarz. Dies muss jedoch nicht so bleiben.
Im Anhang finden Sie außerdem ein Plakat. Ggf. können Sie für das Flaschendesign einige nostalgische Elemente davon übernehmen.

```html
<!DOCTYPE html>
<html lang="de">
<head>
<meta charset="utf-8">
<title>Muskattrollinger Rosé – Etikett</title>
<link href="https://fonts.googleapis.com/css2?family=Cormorant+Garamond:wght@500;600;700&family=Mrs+Saint+Delafield&display=swap" rel="stylesheet">
<style>
  :root {
    --stage: #3b1c12;
    --band: #000000;
    --paper-light: #f2f2f2;
    --paper-mid: #dcdcdc;
    --ink: #111111;
    --white: #ffffff;
    --rust: #c1461f;
    --grape-dark: #3a3a3a;
    --grape-light: #9a9a9a;
  }
  html, body {
    margin: 0;
    padding: 0;
    width: 1100px;
    height: 1200px;
    overflow: hidden;
    background: var(--stage);
  }
  .canvas {
    position: relative;
    width: 1100px;
    height: 1200px;
  }
  .label {
    position: absolute;
    left: 50px;
    top: 191px;
    width: 1000px;
    height: 818px;
    background: linear-gradient(160deg, var(--paper-light) 0%, #e9e9e9 45%, var(--paper-mid) 100%);
    font-family: "Cormorant Garamond", Georgia, serif;
    overflow: hidden;
    box-shadow: 0 8px 24px rgba(0,0,0,0.45);
  }
  .band-top {
    position: absolute;
    left: 0; top: 0;
    width: 100%;
    height: 148px;
    background: var(--band);
    border-bottom: 4px solid var(--white);
  }
  .region {
    position: absolute;
    left: 0; width: 100%;
    top: 22px;
    margin: 0;
    text-align: center;
    color: var(--white);
    font-weight: 700;
    font-size: 84px;
    line-height: 1;
    letter-spacing: 1px;
  }
  .vintage {
    position: absolute;
    left: 575px;
    top: 108px;
    color: var(--rust);
    font-weight: 600;
    font-size: 38px;
    line-height: 1;
  }
  .grapes {
    position: absolute;
    left: 706px;
    top: 154px;
    width: 294px;
    height: 340px;
    background: radial-gradient(ellipse at 55% 50%, var(--grape-dark) 0%, #6a6a6a 45%, rgba(154,154,154,0.35) 75%, rgba(220,220,220,0) 100%);
  }
  .variety {
    position: absolute;
    margin: 0;
    color: var(--rust);
    font-family: "Mrs Saint Delafield", cursive;
    font-weight: 400;
    line-height: 1;
  }
  .variety-name {
    left: 248px;
    top: 200px;
    font-size: 112px;
  }
  .variety-style {
    left: 500px;
    top: 290px;
    font-size: 112px;
  }
  .quality {
    position: absolute;
    left: 0; width: 100%;
    top: 482px;
    text-align: center;
    color: var(--ink);
    font-weight: 600;
    font-size: 30px;
    line-height: 45px;
    letter-spacing: 1px;
  }
  .legal {
    position: absolute;
    left: 0; width: 100%;
    top: 604px;
    text-align: center;
    color: var(--rust);
    font-weight: 600;
    font-size: 25px;
    line-height: 38px;
  }
  .abv {
    position: absolute;
    left: 79px;
    top: 645px;
    color: var(--ink);
    font-weight: 600;
    font-size: 30px;
    line-height: 1;
  }
  .sulfite {
    position: absolute;
    left: 81px;
    top: 686px;
    color: var(--rust);
    font-weight: 600;
    font-size: 22px;
    line-height: 1;
  }
  .volume {
    position: absolute;
    left: 825px;
    top: 672px;
    color: var(--ink);
    font-weight: 600;
    font-size: 38px;
    line-height: 1;
  }
  .band-bottom {
    position: absolute;
    left: 0; bottom: 0;
    width: 100%;
    height: 86px;
    background: var(--band);
    border-top: 4px solid var(--white);
    display: flex;
    align-items: center;
    justify-content: center;
    color: var(--white);
    font-weight: 700;
    font-size: 25px;
    letter-spacing: 0.3px;
  }
  .dot {
    color: var(--rust);
    margin: 0 10px;
    font-size: 20px;
  }
</style>
</head>
<body>
<div class="canvas">
  <section class="label">
    <header class="band-top">
      <h1 class="region">Württemberg</h1>
      <span class="vintage">2019 er</span>
    </header>

    <div class="grapes" role="img" aria-label="Gravierte Weintraube mit Rebblatt"></div>

    <h2 class="variety variety-name">Muskattrollinger</h2>
    <h2 class="variety variety-style">Rosé</h2>

    <p class="quality">DEUTSCHER<br>QUALITÄTSWEIN</p>

    <p class="legal" style="margin:0">A.P.Nr. 581 273 64<br>Abfüller D-BWW 581<br>vermarkted durch: Lukas Hemmert</p>

    <span class="abv">11,0% Vol.</span>
    <span class="sulfite">Enthalten Sulfit</span>
    <span class="volume">0,75 l</span>

    <footer class="band-bottom">
      Kelterweg 5<span class="dot">•</span>D-71234 Rebenhausen - Talheimsfeld<span class="dot">•</span>Tel. 071 22/5083614
    </footer>
  </section>
</div>
</body>
</html>
```